Responsive OnePage Design for recruitment company

BrightHire is a modern company that sources interim people for its customers. Mostly developers, scrum master, project managers and designers. In this website we want to tell something about us, about how we work, our customers and we want our candidates be able to subscribe. The subscription form should be several fields (name, surname, email address, phone number and the possibility to upload your resume.We want it to fit into a existing wordpress plugin. We also want a listing of our job opportunities. The listing should be designed in a clear readable overview and if you click on the job you should get the details and be able to respond quickly by filling in you name, surname, email address, rate, phone number and upload your resume. We want this to be a standard configurable plugin. It should be easy to fill in the jobs in Wordpress by our administrator. We want a fresh, modern and cool design. It should be a responsive onepage design. If you click on a listed job you should stay on the same page. Our logo is added.

Target Market(s)

recruitment

Industry/Entity Type

Recruitment

Font styles to use
Sans Serif

Colors

Designer to choose colors to be used in the design.

Requirements
Must have
• Onepage design
• listing of job opportunities
• subscription forms
• be responsive

```html
<!DOCTYPE html>
<html lang="en">
<head>
<meta charset="utf-8">
<title>BrightHire – Recruitment</title>
<link href="https://fonts.googleapis.com/css2?family=Roboto:wght@300;400;500;700&display=swap" rel="stylesheet">
<style>
:root{
  --blue:#1565c0;
  --blue-bright:#1a7fd6;
  --navy:#0d3d8c;
  --green:#1e9e6a;
  --green-btn:#2db87a;
  --teal:#28c08a;
  --ink:#1f1f1f;
  --text:#444;
  --muted:#666;
  --light:#f4f4f4;
  --card-head:#ececec;
  --footer:#161616;
  --white:#fff;
}
*{box-sizing:border-box;margin:0;padding:0}
html,body{width:1200px;height:4423px;overflow:hidden}
body{font-family:'Roboto',Arial,sans-serif;color:var(--text);background:var(--white);position:relative}
section,header,footer,div,form,nav,article{position:absolute}
.topbar{left:0;top:0;width:1200px;height:35px;background:var(--blue-bright);color:var(--white);font-size:13px;z-index:3}
.topbar .contact{left:90px;top:9px;display:flex;gap:22px}
.topbar .contact span{display:flex;align-items:center;gap:6px}
.topbar .auth{right:88px;top:0;display:flex;height:35px}
.topbar .auth a{color:var(--white);text-decoration:none;padding:10px 16px;font-size:12px}
.topbar .auth .register{background:var(--navy)}
.nav{left:0;top:35px;width:1200px;height:112px;background:var(--white)}
.brand{left:88px;top:38px;font-size:32px;font-weight:500;letter-spacing:6px;color:var(--ink)}
.nav ul{position:absolute;right:88px;top:46px;display:flex;gap:28px;list-style:none;font-size:16px;color:#333}
.nav ul .active{color:var(--blue-bright)}
.hero{left:0;top:147px;width:1200px;height:525px;background:linear-gradient(180deg,#26303c 0%,#3b4550 55%,#1d232b 100%)}
.hero h1{position:absolute;width:100%;top:160px;text-align:center;color:var(--white);font-size:70px;font-weight:500}
.hero p{position:absolute;width:100%;top:262px;text-align:center;color:var(--white);font-size:34px;font-weight:300}
.hero .dots{right:38px;top:200px;display:flex;flex-direction:column;gap:10px}
.hero .dots i{display:block;width:9px;height:9px;border-radius:50%;background:var(--white)}
.hero .dots i:first-child{background:var(--blue-bright)}
.search{left:88px;top:610px;width:1023px;height:98px;background:var(--blue);box-shadow:0 6px 18px rgba(0,0,0,.25);z-index:2}
.search .select{top:22px;height:56px;background:var(--white);border-radius:3px;font-size:17px;color:#333;padding:18px 16px;width:258px}
.search .select::after{content:"";position:absolute;right:18px;top:25px;border:7px solid transparent;border-top-color:#333}
.search .btn{left:855px;top:20px;width:143px;height:58px;background:var(--teal);color:var(--white);font-size:22px;text-align:center;line-height:58px;border-radius:3px}
.listing{left:0;top:672px;width:1200px;height:1150px;background:var(--light)}
.section-title{position:absolute;width:100%;text-align:center;font-size:46px;font-weight:400;color:var(--ink)}
.listing .lead{position:absolute;width:100%;top:200px;text-align:center;font-size:19px;color:#333}
.job{width:478px;height:185px;background:var(--white);box-shadow:0 2px 10px rgba(0,0,0,.12)}
.job .job-head{left:0;top:0;width:100%;height:52px;background:var(--card-head);padding:14px 28px;font-size:21px;color:var(--blue-bright)}
.job .apply{position:absolute;right:28px;top:11px;background:var(--green-btn);color:var(--white);font-size:15px;padding:6px 12px;border-radius:3px}
.job dl{position:absolute;left:28px;top:70px;font-size:16px;color:#222;line-height:33px}
.job dt{display:inline;font-weight:700}
.job dd{display:inline;font-weight:400}
.more{left:445px;top:997px;width:310px;height:38px;border:2px solid var(--blue-bright);color:var(--navy);font-size:16px;text-align:center;line-height:34px;background:var(--white)}
.about{left:0;top:1822px;width:1200px;height:572px;background:var(--green)}
.about .frame{left:74px;top:109px;width:427px;height:316px;border:2px solid rgba(255,255,255,.8)}
.about .photo{left:103px;top:138px;width:448px;height:337px;background:linear-gradient(135deg,#5a6f7e,#c9d3d8 55%,#7a8a92)}
.about .play{position:absolute;left:295px;top:275px;width:64px;height:64px}
.about h2{position:absolute;left:596px;top:148px;font-size:42px;font-weight:400;color:var(--white)}
.about p{position:absolute;left:596px;top:220px;width:510px;font-size:15px;line-height:27px;color:var(--white)}
.about .read{left:596px;top:430px;background:var(--navy);color:var(--white);font-size:16px;padding:8px 18px}
.how{left:0;top:2394px;width:1200px;height:681px;background:var(--white)}
.how .section-title{top:116px}
.step{width:360px;top:247px;text-align:center}
.step svg{display:block;margin:0 auto}
.step h3{margin-top:24px;font-size:22px;font-weight:400;color:var(--ink)}
.step p{margin:16px auto 0;width:310px;font-size:15px;line-height:26px;color:#333}
.cta{left:0;top:3075px;width:1200px;height:306px;background:linear-gradient(90deg,#0b5cc4,#1878d6 50%,#0b5cc4)}
.cta h2{position:absolute;width:100%;top:62px;text-align:center;font-size:46px;font-weight:400;color:var(--white)}
.cta p{position:absolute;width:100%;top:130px;text-align:center;font-size:21px;color:var(--white)}
.cta .btn{left:510px;top:188px;width:183px;height:57px;border:3px solid var(--white);color:var(--white);font-size:28px;text-align:center;line-height:51px}
.subscribe{left:0;top:3381px;width:1200px;height:619px;background:linear-gradient(90deg,#fff 0%,#f6f9fc 60%,#e8eff6 100%)}
.subscribe h2{position:absolute;left:91px;top:114px;font-size:40px;font-weight:400;color:var(--ink)}
.field{height:47px;border:1px solid #bbb;background:var(--white);font-size:15px;color:#333;padding:14px 12px}
.field .choose{display:inline-block;background:#ddd;border:1px solid #aaa;padding:4px 12px;margin:-6px 10px 0 0;font-size:14px}
.submit{left:97px;top:425px;width:124px;height:35px;border:2px solid var(--blue-bright);border-radius:18px;color:var(--blue-bright);font-size:18px;text-align:center;line-height:31px}
.subscribe .person{left:796px;top:68px;width:404px;height:551px;background:linear-gradient(180deg,#c7d6e4,#8aa8c4 50%,#3a4d64)}
.footer{left:0;top:4000px;width:1200px;height:423px;background:var(--footer);color:var(--white)}
.footer h4{font-size:19px;font-weight:400;margin-bottom:28px}
.footer ul{list-style:none;font-size:14px;line-height:26px}
.col{top:80px}
.contact-list li{display:flex;gap:22px;margin-bottom:18px;line-height:18px}
.links li::before{content:"•";margin-right:12px}
.social li{display:flex;align-items:center;gap:10px;margin-bottom:16px}
.newsletter .input{position:relative;width:272px;height:38px;background:var(--white);color:#333;font-size:15px;padding:10px 12px;margin-bottom:12px}
.newsletter .send{position:relative;width:124px;height:38px;background:var(--navy);text-align:center;line-height:38px;font-size:17px}
.copyright{left:0;top:360px;width:1200px;text-align:center;font-size:14px;color:#ddd}
</style>
</head>
<body>

<header class="topbar">
  <div class="contact">
    <span><svg width="12" height="12" viewBox="0 0 24 24"><path fill="#fff" d="M6.6 10.8a15 15 0 0 0 6.6 6.6l2.2-2.2c.3-.3.7-.4 1-.2 1.1.4 2.3.6 3.6.6.6 0 1 .4 1 1V20c0 .6-.4 1-1 1A17 17 0 0 1 3 4c0-.6.4-1 1-1h3.5c.6 0 1 .4 1 1 0 1.3.2 2.5.6 3.6.1.3 0 .7-.2 1z"/></svg>+10 (0) 555 210 347</span>
    <span><svg width="13" height="10" viewBox="0 0 24 18"><rect width="24" height="18" rx="2" fill="#fff"/><path d="M1 2l11 8 11-8" stroke="#1a7fd6" stroke-width="2" fill="none"/></svg>hello@brighthire.example</span>
  </div>
  <div class="auth"><a>Login</a><a class="register">Register</a></div>
</header>

<nav class="nav">
  <div class="brand">BRIGHTHIRE</div>
  <ul><li class="active">Home</li><li>About us</li><li>How we work</li><li>Job</li><li>Subscription</li><li>Contact us</li></ul>
</nav>

<section class="hero" role="img" aria-label="Night view of a city skyline with tall office towers">
  <h1>BrightHire</h1>
  <p>Neque porro quisquam est qui dolorem</p>
  <div class="dots"><i></i><i></i><i></i><i></i></div>
</section>

<form class="search">
  <div class="select" style="left:24px">Job Title</div>
  <div class="select" style="left:302px">Skill</div>
  <div class="select" style="left:580px">Location</div>
  <div class="btn">Search</div>
</form>

<section class="listing">
  <h2 class="section-title" style="top:126px">LISTING OF JOB</h2>
  <p class="lead">Neque porro quisquam est qui dolorem ipsum quia dolor sit amet</p>

  <article class="job" style="left:100px;top:310px"><div class="job-head">Mostly Developers<span class="apply">Apply Now</span></div><dl><dt>Keyskills</dt><dd> : Neque porro quisquam est qui</dd><br><dt>Location</dt><dd> : Delhi</dd><br><dt>Experience</dt><dd> : 3-5 years</dd></dl></article>
  <article class="job" style="left:613px;top:310px"><div class="job-head">Scrum Master<span class="apply">Apply Now</span></div><dl><dt>Keyskills</dt><dd> : Neque porro quisquam est qui</dd><br><dt>Location</dt><dd> : Delhi</dd><br><dt>Experience</dt><dd> : 3-5 years</dd></dl></article>
  <article class="job" style="left:100px;top:528px"><div class="job-head">Project Managers<span class="apply">Apply Now</span></div><dl><dt>Keyskills</dt><dd> : Neque porro quisquam est qui</dd><br><dt>Location</dt><dd> : Delhi</dd><br><dt>Experience</dt><dd> : 3-5 years</dd></dl></article>
  <article class="job" style="left:613px;top:528px"><div class="job-head">Designers<span class="apply">Apply Now</span></div><dl><dt>Keyskills</dt><dd> : Neque porro quisquam est qui</dd><br><dt>Location</dt><dd> : Delhi</dd><br><dt>Experience</dt><dd> : 3-5 years</dd></dl></article>
  <article class="job" style="left:100px;top:749px"><div class="job-head">Mostly Developers<span class="apply">Apply Now</span></div><dl><dt>Keyskills</dt><dd> : Neque porro quisquam est qui</dd><br><dt>Location</dt><dd> : Delhi</dd><br><dt>Experience</dt><dd> : 3-5 years</dd></dl></article>
  <article class="job" style="left:613px;top:749px"><div class="job-head">Scrum Master<span class="apply">Apply Now</span></div><dl><dt>Keyskills</dt><dd> : Neque porro quisquam est qui</dd><br><dt>Location</dt><dd> : Delhi</dd><br><dt>Experience</dt><dd> : 3-5 years</dd></dl></article>

  <div class="more">VIEW MORE SEARCH RESULTS</div>
</section>

<section class="about">
  <div class="frame"></div>
  <div class="photo" role="img" aria-label="Two business people in a meeting at an office table"></div>
  <svg class="play" viewBox="0 0 64 64"><circle cx="32" cy="32" r="30" fill="rgba(0,0,0,.35)" stroke="#fff" stroke-width="2"/><path d="M26 20l18 12-18 12z" fill="#fff"/></svg>
  <h2>ABOUT US</h2>
  <p>It is a long established fact that a reader will be distracted by the readable content of a page when looking at its layout. The point of using Lorem Ipsum is that it has a more-or-less normal distribution of letters, as opposed to using 'Content here, content here', making it look like readable English. Many desktop publishing packages and web page editors now use Lorem Ipsum as their default model text, and a search for 'lorem ipsum' will uncover many web sites still in their infancy</p>
  <div class="read">Read More</div>
</section>

<section class="how">
  <h2 class="section-title">HOW WE WORK</h2>
  <div class="step" style="left:59px">
    <svg width="136" height="136" viewBox="0 0 136 136"><circle cx="68" cy="68" r="66" fill="none" stroke="#1a7fd6" stroke-width="2"/><circle cx="68" cy="68" r="56" fill="#1565c0"/><rect x="48" y="50" width="40" height="28" rx="2" fill="none" stroke="#fff" stroke-width="4"/><path d="M62 84h12M68 78v6" stroke="#fff" stroke-width="4"/></svg>
    <h3>Porro Quisquam</h3>
    <p>Many desktop publishing packages and web page editors now use Lorem Ipsum as their default</p>
  </div>
  <div class="step" style="left:419px">
    <svg width="136" height="136" viewBox="0 0 136 136"><circle cx="68" cy="68" r="66" fill="none" stroke="#1a7fd6" stroke-width="2"/><circle cx="68" cy="68" r="56" fill="#1565c0"/><circle cx="68" cy="58" r="7" fill="#fff"/><circle cx="52" cy="62" r="5" fill="#fff"/><circle cx="84" cy="62" r="5" fill="#fff"/><path d="M55 80a13 11 0 0 1 26 0z M42 78a10 8 0 0 1 16-2v2z M94 78a10 8 0 0 0-16-2v2z" fill="#fff"/></svg>
    <h3>Dolorem Ipsum quia</h3>
    <p>Many desktop publishing packages and web page editors now use Lorem Ipsum as their default</p>
  </div>
  <div class="step" style="left:779px">
    <svg width="136" height="136" viewBox="0 0 136 136"><circle cx="68" cy="68" r="66" fill="none" stroke="#1a7fd6" stroke-width="2"/><circle cx="68" cy="68" r="56" fill="#1565c0"/><circle cx="68" cy="68" r="22" fill="none" stroke="#fff" stroke-width="4"/><path d="M58 68l8 8 18-20" fill="none" stroke="#fff" stroke-width="4"/></svg>
    <h3>Neque porro dolor</h3>
    <p>Many desktop publishing packages and web page editors now use Lorem Ipsum as their default model text,</p>
  </div>
</section>

<section class="cta">
  <h2>Save time by finding the right employe</h2>
  <p>Over 1 million interactions, 50,000 success stories Make yours now.</p>
  <div class="btn">Click Here</div>
</section>

<section class="subscribe">
  <h2>SUBSCRIPTION</h2>
  <div class="field" style="left:91px;top:204px;width:251px">Your Name</div>
  <div class="field" style="left:360px;top:204px;width:247px">surname</div>
  <div class="field" style="left:91px;top:266px;width:251px">Email address</div>
  <div class="field" style="left:360px;top:266px;width:247px">Phone number</div>
  <div class="field" style="left:91px;top:334px;width:516px"><span class="choose">Choose File</span>upload your resume</div>
  <div class="submit">Submit</div>
  <div class="person" role="img" aria-label="Smiling businessman in shirt and tie holding a laptop"></div>
</section>

<footer class="footer">
  <div class="col" style="left:88px;width:300px">
    <h4>CONTACT US</h4>
    <ul class="contact-list">
      <li><svg width="12" height="16" viewBox="0 0 12 16"><path d="M6 0a6 6 0 0 1 6 6c0 4-6 10-6 10S0 10 0 6a6 6 0 0 1 6-6z" fill="#fff"/><circle cx="6" cy="6" r="2" fill="#161616"/></svg><span>Level 12/8 Harbour Lane<br>Westport , WP 4100<br>Northland</span></li>
      <li><svg width="12" height="12" viewBox="0 0 24 24"><path fill="#fff" d="M6.6 10.8a15 15 0 0 0 6.6 6.6l2.2-2.2c.3-.3.7-.4 1-.2 1.1.4 2.3.6 3.6.6.6 0 1 .4 1 1V20c0 .6-.4 1-1 1A17 17 0 0 1 3 4c0-.6.4-1 1-1h3.5c.6 0 1 .4 1 1 0 1.3.2 2.5.6 3.6.1.3 0 .7-.2 1z"/></svg><span>+10 (0) 555 210 347</span></li>
      <li><svg width="13" height="10" viewBox="0 0 24 18"><rect width="24" height="18" rx="2" fill="#fff"/><path d="M1 2l11 8 11-8" stroke="#161616" stroke-width="2" fill="none"/></svg><span>hello@brighthire.example</span></li>
    </ul>
  </div>
  <div class="col" style="left:419px">
    <h4>QUICK LINKS</h4>
    <ul class="links"><li>Home</li><li>About us</li><li>News</li><li>Services</li><li>Contact Us</li></ul>
  </div>
  <div class="col" style="left:628px">
    <h4>FOLLOW US</h4>
    <ul class="social">
      <li><svg width="28" height="28"><circle cx="14" cy="14" r="12" fill="none" stroke="#fff" stroke-width="1.5"/></svg>Updates</li>
      <li><svg width="28" height="28"><circle cx="14" cy="14" r="12" fill="none" stroke="#fff" stroke-width="1.5"/></svg>Short news</li>
      <li><svg width="28" height="28"><circle cx="14" cy="14" r="12" fill="none" stroke="#fff" stroke-width="1.5"/></svg>Community</li>
    </ul>
  </div>
  <div class="col newsletter" style="left:837px">
    <h4>NEWSLETTER</h4>
    <div class="input">Your Name</div>
    <div class="input">Email address</div>
    <div class="send">SEND</div>
  </div>
  <div class="copyright">© Copyright 2019 . All Rights Reserved.</div>
</footer>

</body>
</html>
```